Fee Detective - Website Design

Create website designs for new FeeDetective.com web application.
We are looking for a clean, playful design based on the attached wireframes and the images we have collected on our PinVault board for inspiration : https://app.pinvault-example.net/7QrTb2kZw4Xc81?p=3Hyd9mLe5Rf
Users of the site will want to be able to quickly run a search using the transaction descriptor they want to identify and see any matching merchants. If they don't get a match then we need then to be able to easily provide further details so we can try and find a match for them
Target Market(s)
Anyone with a bank account
Number of Pages Required
5+ page
Requirements
Must have
- Clean yet playful design, incorporating the themes from our pinvault board

```html
<!DOCTYPE html>
<html lang="en">
<head>
<meta charset="utf-8">
<title>Fee Detective – Website Screens</title>
<link href="https://fonts.googleapis.com/css2?family=Roboto:wght@400;500;700&display=swap" rel="stylesheet">
<style>
  :root {
    --stage: #9a9a9a;
    --cream-top: #fbf1dc;
    --cream-mid: #fde8c4;
    --cream-bottom: #fdd6a2;
    --brand: #e8891a;
    --ink: #1d1d1d;
    --body: #2f2f2f;
    --field: #ffffff;
    --field-line: #d9d9d9;
    --toggle: #dedede;
    --row-warm: rgba(247, 196, 120, 0.45);
    --row-light: rgba(253, 236, 205, 0.55);
  }
  * { box-sizing: border-box; margin: 0; padding: 0; }
  html, body { width: 1200px; height: 911px; overflow: hidden; }
  body {
    background: var(--stage);
    font-family: "Roboto", Arial, sans-serif;
    position: relative;
  }
  .screen {
    position: absolute;
    width: 543px;
    overflow: hidden;
    background:
      radial-gradient(circle at 75% 75%, rgba(255,255,255,0.45) 0 18%, transparent 40%),
      radial-gradient(circle at 35% 30%, rgba(210,200,180,0.18) 0 22%, transparent 23%),
      linear-gradient(170deg, var(--cream-top) 0%, var(--cream-mid) 55%, var(--cream-bottom) 100%);
  }
  .screen--home    { left: 41px;  top: 36px;  height: 305px; }
  .screen--suggest { left: 616px; top: 36px;  height: 305px; }
  .screen--results { left: 41px;  top: 374px; height: 501px; }
  .screen--nomatch { left: 616px; top: 374px; height: 363px; }

  .mascot {
    position: absolute; left: 460px; top: 5px; width: 78px; height: 96px;
    border-radius: 40px 40px 12px 12px;
    background: linear-gradient(180deg, #6d6d6d 0%, #e9c9a0 45%, #a8753f 100%);
    opacity: 0.85;
  }
  .brand-title {
    position: absolute; left: 0; right: 0; top: 54px;
    text-align: center;
    color: var(--brand);
    font-size: 31px; font-weight: 500; line-height: 36px;
  }
  .tagline {
    position: absolute; left: 30px; right: 30px; top: 105px;
    text-align: center; font-size: 11px; line-height: 15px; color: var(--body);
  }
  .search {
    position: absolute; left: 71px; top: 160px; width: 401px; height: 32px;
    background: var(--field);
    box-shadow: 0 1px 3px rgba(0,0,0,0.12);
    display: flex; align-items: center;
  }
  .search__icon { width: 28px; display: flex; justify-content: center; }
  .search__icon svg { width: 10px; height: 10px; }
  .search__divider { width: 1px; height: 20px; background: var(--field-line); }
  .search__value { flex: 1; padding-left: 9px; font-size: 8px; color: var(--ink); }
  .search__toggle {
    width: 24px; height: 22px; margin-right: 10px; background: var(--toggle);
    display: flex; align-items: center; justify-content: center;
  }
  .search__toggle svg { width: 8px; height: 6px; }
  .help-link {
    position: absolute; right: 71px; top: 199px;
    font-size: 11px; color: var(--brand);
  }
  .suggestions {
    position: absolute; left: 71px; top: 192px; width: 401px; height: 60px;
    background: var(--field); list-style: none; padding: 10px 0 0 36px;
  }
  .suggestions li {
    display: flex; align-items: center; gap: 6px;
    font-size: 8px; color: var(--ink); height: 14.5px;
  }
  .suggestions svg { width: 8px; height: 7px; }

  .section-title {
    position: absolute; left: 0; right: 0; text-align: center;
    font-weight: 500; color: var(--ink);
  }
  .matches-title { top: 233px; font-size: 13.5px; }
  .matches {
    position: absolute; left: 29px; top: 257px; width: 486px;
    border-collapse: collapse; border: 1px solid var(--brand);
    font-size: 10px; color: var(--ink);
  }
  .matches th {
    background: var(--brand); color: #fff; font-weight: 400; font-size: 10.5px;
    height: 26px; text-align: left; padding-left: 16px;
  }
  .matches td { height: 34px; padding-left: 16px; }
  .matches th + th, .matches td + td { border-left: 3px solid rgba(255,240,220,0.9); }
  .matches tbody tr:nth-child(odd) td { background: var(--row-warm); }
  .matches tbody tr:nth-child(even) td { background: var(--row-light); }
  .col-name { width: 213px; }
  .col-conf { width: 164px; }
  .matches td.col-action { padding-left: 14px; }
  .btn {
    display: inline-block; background: var(--brand); color: #fff;
    border-radius: 4px; text-align: center; font-size: 9.5px;
  }
  .btn--small { width: 79px; height: 18px; line-height: 18px; }
  .btn--wide { width: 125px; height: 18px; line-height: 18px; }
  .crowd {
    position: absolute; left: 20px; right: 20px; text-align: center;
    font-size: 11px; line-height: 15px; color: var(--body);
  }
  .crowd-cta { position: absolute; left: 0; right: 0; text-align: center; }
  .screen--results .crowd { top: 414px; }
  .screen--results .crowd-cta { top: 460px; }
  .nomatch-title { top: 238px; font-size: 17px; font-weight: 700; }
  .screen--nomatch .crowd { top: 276px; }
  .screen--nomatch .crowd-cta { top: 323px; }
</style>
</head>
<body>

<svg width="0" height="0" style="position:absolute">
  <defs>
    <symbol id="icon-search" viewBox="0 0 24 24"><circle cx="10" cy="10" r="7" fill="none" stroke="#777" stroke-width="2.5"/><line x1="15" y1="15" x2="22" y2="22" stroke="#777" stroke-width="2.5"/></symbol>
    <symbol id="icon-down" viewBox="0 0 8 6"><polyline points="1,1 4,4 7,1" fill="none" stroke="#fff" stroke-width="1.6"/></symbol>
    <symbol id="icon-up" viewBox="0 0 8 6"><polyline points="1,5 4,2 7,5" fill="none" stroke="#fff" stroke-width="1.6"/></symbol>
    <symbol id="icon-trend" viewBox="0 0 8 7"><polyline points="0.5,0 0.5,6.5 8,6.5" fill="none" stroke="#333" stroke-width="0.9"/><polyline points="1.5,5 3.5,3 5,4.2 7.5,1.5" fill="none" stroke="#333" stroke-width="0.9"/></symbol>
  </defs>
</svg>

<section class="screen screen--home">
  <div class="mascot" role="img" aria-label="Cartoon detective mascot with hat and magnifying glass"></div>
  <h1 class="brand-title">Fee Detective</h1>
  <p class="tagline">Helping you identify those odd and sometimes surprising charges on your bank statements<br>and transaction feeds!</p>
  <div class="search">
    <span class="search__icon"><svg><use href="#icon-search"/></svg></span><span class="search__divider"></span>
    <span class="search__value">Enter your transaction descriptor...</span>
    <span class="search__toggle"><svg><use href="#icon-down"/></svg></span>
  </div>
  <a class="help-link">What is a Transaction Descriptor?</a>
</section>

<section class="screen screen--suggest">
  <div class="mascot" role="img" aria-label="Cartoon detective mascot with hat and magnifying glass"></div>
  <h1 class="brand-title">Fee Detective</h1>
  <p class="tagline">Helping you identify those odd and sometimes surprising charges on your bank statements<br>and transaction feeds!</p>
  <div class="search">
    <span class="search__icon"><svg><use href="#icon-search"/></svg></span><span class="search__divider"></span>
    <span class="search__value">GREENM</span>
    <span class="search__toggle"><svg><use href="#icon-up"/></svg></span>
  </div>
  <ul class="suggestions">
    <li><svg><use href="#icon-trend"/></svg>GREENMART PTY LTD ST IVES AU</li>
    <li><svg><use href="#icon-trend"/></svg>GREENMART ONLINE SERVICES AU220223</li>
    <li><svg><use href="#icon-trend"/></svg>GREENWORKS CLOTHING CO SYDNEY</li>
  </ul>
</section>

<section class="screen screen--results">
  <div class="mascot" role="img" aria-label="Cartoon detective mascot with hat and magnifying glass"></div>
  <h1 class="brand-title">Fee Detective</h1>
  <p class="tagline">Helping you identify those odd and sometimes surprising charges on your bank statements<br>and transaction feeds!</p>
  <div class="search">
    <span class="search__icon"><svg><use href="#icon-search"/></svg></span><span class="search__divider"></span>
    <span class="search__value">GREENMART PTY LTD ST IVES AU</span>
    <span class="search__toggle"><svg><use href="#icon-down"/></svg></span>
  </div>
  <a class="help-link">What is a Transaction Descriptor?</a>
  <h2 class="section-title matches-title">Top Matches</h2>
  <table class="matches">
    <thead><tr><th class="col-name">Merchant Name</th><th class="col-conf">confidence</th><th></th></tr></thead>
    <tbody>
      <tr><td>Greenmart Pty Ltd</td><td>High</td><td class="col-action"><span class="btn btn--small">View Details</span></td></tr>
      <tr><td>Greenmart Clothing Co</td><td>Low</td><td class="col-action"><span class="btn btn--small">View Details</span></td></tr>
      <tr><td>Greenmart Online Plc</td><td>Low</td><td class="col-action"><span class="btn btn--small">View Details</span></td></tr>
    </tbody>
  </table>
  <p class="crowd">Couldn't fnd a match? Help us Crowd Source more data by clicking the button below and providing<br>a few details so we can help fnd it and make it available to everyone</p>
  <div class="crowd-cta"><span class="btn btn--wide">Help Improve Our Results</span></div>
</section>

<section class="screen screen--nomatch">
  <div class="mascot" role="img" aria-label="Cartoon detective mascot with hat and magnifying glass"></div>
  <h1 class="brand-title">Fee Detective</h1>
  <p class="tagline">Helping you identify those odd and sometimes surprising charges on your bank statements<br>and transaction feeds!</p>
  <div class="search">
    <span class="search__icon"><svg><use href="#icon-search"/></svg></span><span class="search__divider"></span>
    <span class="search__value">GREENMART PTY LTD ST IVES AU</span>
    <span class="search__toggle"><svg><use href="#icon-down"/></svg></span>
  </div>
  <a class="help-link">What is a Transaction Descriptor?</a>
  <h2 class="section-title nomatch-title">Hmmm, we couldn't find a match!</h2>
  <p class="crowd">Couldn't fnd a match? Help us Crowd Source more data by clicking the button below and providing<br>a few details so we can help fnd it and make it available to everyone</p>
  <div class="crowd-cta"><span class="btn btn--wide">Help Improve Our Results</span></div>
</section>

</body>
</html>
```